established boer goat stud and dorper sheep stud need an updated look

I need a design to promote the boer goat stud and dorper sheep stud, so its clear and simple
Updates

Details for business card design Wirrabel Boers and Dorper Sheep Stud. I would like silhouette animal head or full body of a boer goat (not a dairy breed goat) and Dorper sheep. Contact: Maree Dalton +61 412578304 Sandra Pollock +61 438615027 Mooroopna North Victoria Australia Email: wirrabel5184@mailvane.com

Industry/Entity Type

Agriculture

Contact Information for Business Card

Wirrabel Boers and Dorper Sheep Stud Maree Dalton +61 412578304 Sandra Pollock +61 438615027 wirrabel5184@mailvane.com Bellmara Victoria Australia

Colors
EE7325
F08F49
F5BC92
FAE3D3
FDF4ED

Requirements
Must have
• My Boer Goats and Dorper Sheep images see my photos

```html
<!DOCTYPE html>
<html lang="en">
<head>
<meta charset="utf-8">
<title>Wirrabel Boers &amp; Dorper Sheep Stud – Business Card</title>
<link href="https://fonts.googleapis.com/css2?family=Oswald:wght@500;700&family=Arimo:wght@400;700&display=swap" rel="stylesheet">
<style>
  :root {
    --page-bg: #2a2a2a;
    --card-white: #ffffff;
    --ink: #111111;
    --text-light: #ffffff;
    --pasture-dark: #56632f;
    --pasture-mid: #76863f;
    --fleece: #d9d2c0;
    --soil: #7d6447;
    --curve-line: #111111;
  }
  * { margin: 0; padding: 0; box-sizing: border-box; }
  html, body {
    width: 1200px;
    height: 930px;
    overflow: hidden;
    background: var(--page-bg);
  }
  .canvas {
    width: 1200px;
    height: 930px;
    display: flex;
    flex-direction: column;
    align-items: center;
    justify-content: center;
    gap: 48px;
  }
  .card {
    position: relative;
    width: 640px;
    height: 366px;
    border-radius: 18px;
    overflow: hidden;
    background: var(--card-white);
  }

  /* Front */
  .front-photo {
    position: absolute;
    inset: 0;
    background:
      linear-gradient(to top, rgba(0,0,0,0.35) 0%, rgba(0,0,0,0) 35%),
      linear-gradient(100deg, var(--pasture-mid) 0%, var(--fleece) 30%, var(--fleece) 55%, var(--soil) 75%, var(--pasture-dark) 100%);
  }
  .front-title {
    position: absolute;
    right: 26px;
    bottom: 22px;
    font-family: "Oswald", sans-serif;
    font-weight: 500;
    font-size: 35px;
    letter-spacing: 0.5px;
    text-transform: uppercase;
    color: var(--text-light);
    line-height: 1;
    white-space: nowrap;
  }

  /* Back */
  .back-art {
    position: absolute;
    inset: 0;
  }
  .brand {
    position: absolute;
    left: 34px;
    top: 172px;
    font-family: "Oswald", sans-serif;
    font-weight: 700;
    text-transform: uppercase;
    color: var(--ink);
    line-height: 0.95;
    white-space: nowrap;
  }
  .brand-main { font-size: 36px; display: block; letter-spacing: 0.3px; }
  .brand-sub { font-size: 19px; display: block; letter-spacing: 0.4px; }
  .contacts {
    position: absolute;
    left: 34px;
    top: 250px;
    font-family: "Arimo", sans-serif;
    font-size: 16px;
    color: var(--ink);
    line-height: 1.4;
    list-style: none;
    white-space: nowrap;
  }
  .contact-name { font-weight: 700; text-transform: uppercase; }
</style>
</head>
<body>
<main class="canvas">

  <section class="card card-front">
    <div class="front-photo" role="img" aria-label="Photo of a Dorper sheep with black head and white body standing on grassy pasture"></div>
    <h1 class="front-title">Wirrabel Boers &amp; Dorper Sheep Stud</h1>
  </section>

  <section class="card card-back">
    <svg class="back-art" width="640" height="366" viewBox="0 0 640 366">
      <defs>
        <linearGradient id="goat-tones" x1="0" y1="0" x2="1" y2="1">
          <stop offset="0" stop-color="#6d7f3e"/>
          <stop offset="0.45" stop-color="#ece8e0"/>
          <stop offset="0.75" stop-color="#b8744a"/>
          <stop offset="1" stop-color="#e3dcd1"/>
        </linearGradient>
      </defs>
      <path role="img" aria-label="Photo of Boer goats with white bodies and brown heads resting on grass"
            d="M250,0 C250,170 420,262 640,250 L640,0 Z" fill="url(#goat-tones)"/>
      <path d="M250,0 C250,170 420,262 640,250" fill="none" stroke="var(--curve-line)" stroke-width="4"/>
    </svg>

    <h2 class="brand">
      <span class="brand-main">Wirrabel Boers</span>
      <span class="brand-sub">&amp; Dorper Sheep Stud</span>
    </h2>

    <ul class="contacts">
      <li><span class="contact-name">Maree Dalton</span> +61 412578304</li>
      <li><span class="contact-name">Sandra Pollock</span> +61 438615027</li>
      <li>Email : wirrabel5184@mailvane.com</li>
      <li>Address : Bellmara Victoria Australia</li>
    </ul>
  </section>

</main>
</body>
</html>
```